Corvelle Meadow Organic Flower Farm, Farmer Florist

I am a flower grower and florist, so I do everything from the field to the vase. I want to include my website, phone, email and instagram

```html
<!DOCTYPE html>
<html lang="en">
<head>
<meta charset="utf-8">
<title>Corvelle Meadow – Business Cards</title>
<link href="https://fonts.googleapis.com/css2?family=Arimo:wght@400;700&display=swap" rel="stylesheet">
<style>
  :root {
    --stage: #2a2522;
    --card: #1c1c1c;
    --green: #4b6a34;
    --green-light: #8fb567;
    --text-grey: #c9c9c9;
    --rule: #5a5a5a;
  }
  html, body {
    margin: 0;
    padding: 0;
    width: 1200px;
    height: 842px;
    overflow: hidden;
    background: var(--stage);
    font-family: "Arimo", Arial, sans-serif;
  }
  .stage {
    position: relative;
    width: 1200px;
    height: 842px;
  }
  .card {
    position: absolute;
    width: 540px;
    height: 310px;
    background: var(--card);
    box-shadow: 0 12px 30px rgba(0,0,0,0.55);
    overflow: hidden;
  }

  /* Contact side */
  .card--contact { left: 50px; top: 430px; }
  .band {
    position: absolute;
    left: 0;
    width: 100%;
    height: 16px;
    background: var(--green);
  }
  .band--top { top: 0; }
  .band--bottom { bottom: 0; }
  .contact {
    position: absolute;
    left: 0;
    right: 0;
    top: 68px;
    text-align: center;
  }
  .contact__name {
    margin: 0;
    color: var(--green);
    font-weight: 700;
    font-size: 24px;
    letter-spacing: 0.5px;
  }
  .contact__role {
    margin: 4px 0 0;
    color: var(--text-grey);
    font-size: 16px;
  }
  .contact__rule {
    width: 170px;
    height: 1px;
    margin: 12px auto 14px;
    background: var(--rule);
  }
  .contact__line {
    margin: 2px 0;
    color: var(--text-grey);
    font-size: 17px;
  }

  /* Brand side */
  .card--brand { left: 610px; top: 110px; }
  .tab {
    position: absolute;
    width: 46px;
    height: 36px;
    background: var(--green);
  }
  .tab::before {
    content: "";
    position: absolute;
    top: 0;
    width: 4px;
    height: 100%;
    background: var(--green-light);
  }
  .tab--top-right { right: 0; top: 40px; }
  .tab--top-right::before { left: 0; }
  .tab--left { left: 0; top: 190px; }
  .tab--left::before { right: 0; }
  .brand {
    position: absolute;
    left: 0;
    right: 0;
    top: 128px;
    display: flex;
    align-items: center;
    justify-content: center;
    gap: 14px;
  }
  .brand__mark {
    width: 18px;
    height: 18px;
    border-radius: 50%;
    background: var(--green);
  }
  .brand__name {
    color: var(--green);
    font-size: 34px;
    font-weight: 400;
    letter-spacing: 3px;
    text-transform: uppercase;
  }
</style>
</head>
<body>
<main class="stage">
  <section class="card card--contact" aria-label="Business card contact side">
    <div class="band band--top"></div>
    <div class="contact">
      <p class="contact__name">ELENA MARSH</p>
      <p class="contact__role">Farmer Florist</p>
      <div class="contact__rule"></div>
      <p class="contact__line">044-987 654 321</p>
      <p class="contact__line">hello@corvellemeadow.com</p>
      <p class="contact__line">www.corvellemeadow.com</p>
      <p class="contact__line">Instagram: @corvellemeadow</p>
    </div>
    <div class="band band--bottom"></div>
  </section>

  <section class="card card--brand" aria-label="Business card brand side">
    <div class="tab tab--top-right"></div>
    <div class="tab tab--left"></div>
    <div class="brand">
      <span class="brand__mark"></span>
      <span class="brand__name">Corvelle Meadow</span>
    </div>
  </section>
</main>
</body>
</html>
```